Professional Photography Business cards

I need business cards that include my logo which I have uploaded. I run a photography business. I am open to ideas but I would like one side to have my logo and the other side to have my contact info. I don't have a website made but I do own a website domain. I have uploaded 2 different logo color schemes. My business colors are Blue, black , and white.

Business Name
Business Phone Number
Business Email
Business Website address
Instagram

Industry/Entity Type

Professional Photography

Contact Information for Business Card

Phone Number: 916-384-7702 email: info@tlane-studio.example Instagram: @t.lanestudio website doman- www.tlane-studio.example

Requirements
Must have
• I like the idea of a business card with a full black background front and back of card. My colors must include royal blue, black, and white

```html
<!DOCTYPE html>
<html lang="en">
<head>
<meta charset="utf-8">
<title>T. Lane Studio — Business Cards</title>
<link href="https://fonts.googleapis.com/css2?family=Arimo:wght@400;700&display=swap" rel="stylesheet">
<style>
  :root {
    --page: #1e1f21;
    --card-black: #1b1c1e;
    --royal-blue: #0a12a6;
    --white: #ffffff;
    --rule: #3a3b3e;
  }
  * { box-sizing: border-box; margin: 0; padding: 0; }
  html, body { width: 1200px; height: 1108px; overflow: hidden; }
  body {
    background: var(--page);
    font-family: "Arimo", Arial, sans-serif;
    color: var(--white);
    position: relative;
  }
  .card {
    position: absolute;
    top: 234px;
    width: 390px;
    height: 640px;
    border-radius: 26px;
    box-shadow: 0 18px 40px rgba(0,0,0,.55);
  }
  .card-front { left: 160px; background: var(--card-black); }
  .card-back  { left: 650px; background: var(--royal-blue); }

  .brand {
    position: absolute;
    left: 0; right: 0;
    top: 120px;
    display: flex;
    align-items: center;
    justify-content: center;
    gap: 14px;
  }
  .brand-mark {
    width: 22px; height: 22px;
    border-radius: 50%;
    background: var(--royal-blue);
    border: 2px solid var(--white);
  }
  .brand-name {
    font-size: 34px;
    font-weight: 400;
    letter-spacing: 1px;
    color: var(--white);
  }

  .contact-list {
    position: absolute;
    left: 0; right: 0;
    top: 270px;
    list-style: none;
  }
  .contact-item {
    display: flex;
    flex-direction: column;
    align-items: center;
    margin-bottom: 26px;
  }
  .contact-icon-row {
    display: flex;
    align-items: center;
    width: 270px;
    gap: 10px;
  }
  .contact-icon-row::before,
  .contact-icon-row::after {
    content: "";
    flex: 1;
    height: 1px;
    background: var(--rule);
  }
  .contact-icon {
    width: 40px; height: 40px;
    border-radius: 50%;
    background: var(--royal-blue);
    display: flex; align-items: center; justify-content: center;
  }
  .contact-icon svg { width: 22px; height: 22px; }
  .contact-icon-plain { background: #c8366f; }
  .contact-text {
    margin-top: 6px;
    font-size: 18px;
    color: var(--white);
  }

  .back-brand {
    position: absolute;
    left: 48px;
    bottom: 90px;
    display: flex;
    align-items: center;
    gap: 14px;
  }
  .back-brand .brand-name { font-size: 40px; }
  .back-brand .brand-mark { background: var(--white); border-color: var(--white); }
</style>
</head>
<body>
  <section class="card card-front" aria-label="Business card, contact side">
    <div class="brand">
      <span class="brand-mark"></span>
      <span class="brand-name">T. Lane Studio</span>
    </div>

    <ul class="contact-list">
      <li class="contact-item">
        <div class="contact-icon-row">
          <span class="contact-icon">
            <svg viewBox="0 0 24 24" fill="none" stroke="#1b1c1e" stroke-width="2" stroke-linejoin="round">
              <path d="M6 3h3l2 5-2.5 1.5a11 11 0 0 0 6 6L16 13l5 2v3a2 2 0 0 1-2 2A16 16 0 0 1 4 5a2 2 0 0 1 2-2z"/>
            </svg>
          </span>
        </div>
        <span class="contact-text">916-384-7702</span>
      </li>
      <li class="contact-item">
        <div class="contact-icon-row">
          <span class="contact-icon">
            <svg viewBox="0 0 24 24" fill="none" stroke="#1b1c1e" stroke-width="2" stroke-linejoin="round">
              <rect x="3" y="6" width="18" height="12"/>
              <path d="M3 6l9 7 9-7"/>
            </svg>
          </span>
        </div>
        <span class="contact-text">info@tlane-studio.example</span>
      </li>
      <li class="contact-item">
        <div class="contact-icon-row">
          <span class="contact-icon">
            <svg viewBox="0 0 24 24" fill="none" stroke="#1b1c1e" stroke-width="1.6">
              <circle cx="12" cy="12" r="9"/>
              <ellipse cx="12" cy="12" rx="4" ry="9"/>
              <path d="M3 12h18M5 7h14M5 17h14"/>
            </svg>
          </span>
        </div>
        <span class="contact-text">www.tlane-studio.example</span>
      </li>
      <li class="contact-item">
        <div class="contact-icon-row">
          <span class="contact-icon contact-icon-plain"></span>
        </div>
        <span class="contact-text">@t.lanestudio</span>
      </li>
    </ul>
  </section>

  <section class="card card-back" aria-label="Business card, brand side">
    <div class="back-brand">
      <span class="brand-mark"></span>
      <span class="brand-name">T. Lane Studio</span>
    </div>
  </section>
</body>
</html>
```